Construction Company looking to change the way General Contractors are perceived today

Looking for a 10-12 page professional web design that includes social media integration, contact form, multiple ways to contact us, services provided, about page, testimonials, project portfolio, downloadable resources, mobile friendly, media gallery, blog, Subcontractors/Bids tab
Must have editing abilities.
I like parallax scrolling, autoplay,
Here is a great example of a site I like. https://marlowstoneworks.com/

Target Market(s)

Commercial and Industrial Owners and Project Managers, Residential Home and Multifamily Owners, Architects and Engineers

Industry/Entity Type

Construction, Pre-construction, Construction Management

Coding

Number of Pages Required

5+ page

Colors

Designer to choose colors to be used in the design.

Requirements
Must have
• TRI-BAY GROUP (Business name) services General Contracting, Construction Management, Pre-construction Services, Home Renovations, Additions, Exterior Spaces, Commercial Construction, Interior buildouts, Office Space Renovations.
Nice to have
• Full-Service General Contractor, Family Oriented - Client Focused, Owner Involved, Relationship Focused, Superior Workmanship, Communication Driven

```html
<!DOCTYPE html>
<html lang="en">
<head>
<meta charset="utf-8">
<title>Tri-Bay Group — General Contractors</title>
<link href="https://fonts.googleapis.com/css2?family=Michroma&family=Oswald:wght@500&family=Open+Sans:wght@400;600;700&display=swap" rel="stylesheet">
<style>
:root{
  --blue:#1a7fe6;
  --blue-dark:#0f63c4;
  --ink:#1d1d1f;
  --text:#555b63;
  --muted:#8a9099;
  --footer:#262626;
  --white:#ffffff;
  --field:#ffffff;
}
*{margin:0;padding:0;box-sizing:border-box}
html,body{width:1200px;height:5155px;overflow:hidden}
body{position:relative;background:var(--white);font-family:"Open Sans",sans-serif;color:var(--text)}
.abs{position:absolute}
.display{font-family:"Michroma",sans-serif;letter-spacing:2px;color:var(--ink);font-weight:400}
.display .hl{color:var(--blue)}
.cond{font-family:"Oswald",sans-serif;font-weight:500;text-transform:uppercase}
.btn{position:absolute;background:var(--blue);color:var(--white);border-radius:22px;display:flex;align-items:center;justify-content:center;font-family:"Oswald",sans-serif;font-size:14px;letter-spacing:.5px;text-transform:uppercase}
.photo{position:absolute}
.band{position:absolute;left:0;width:1200px;background:var(--blue)}
.ring{position:absolute;border-radius:50%;border:2px solid var(--blue)}

/* header */
.header{position:absolute;left:0;top:0;width:1200px;height:112px;background:var(--white)}
.brand{position:absolute;left:112px;top:10px;width:140px;height:140px;border-radius:50%;background:var(--white);border:6px solid var(--blue);display:flex;align-items:center;justify-content:center;z-index:3;box-shadow:0 2px 6px rgba(0,0,0,.15)}
.brand span{font-family:"Michroma",sans-serif;font-size:12px;color:var(--blue);text-align:center;line-height:18px}
.menu{position:absolute;left:688px;top:48px;width:26px}
.menu i{display:block;height:2px;background:var(--blue);margin-bottom:6px}

/* hero */
.hero{position:absolute;left:0;top:112px;width:1200px;height:558px;background:linear-gradient(100deg,#3a3d42 0%,#6e6a64 45%,#c9b9a0 70%,#d8c89a 100%)}
.hero-title{position:absolute;left:110px;top:238px;font-size:29px;line-height:62px;color:var(--white);letter-spacing:3px}
.hero-title .hl{color:var(--blue)}
.dots{position:absolute;display:flex;gap:6px}
.dots i{width:12px;height:12px;border-radius:50%;background:#fff}
.dots i.on{background:var(--blue)}

/* about */
.about-img{left:156px;top:760px;width:360px;height:360px;border-radius:50%;background:linear-gradient(160deg,#d8e3ee,#8a8f96 60%,#4b4a48);border-left:8px solid var(--blue);border-bottom:8px solid var(--blue)}
.about-text{left:598px;top:842px;width:482px;font-size:14.5px;line-height:26px;text-align:justify}

/* services */
.svc{position:absolute;top:1362px;width:302px;height:306px;background:var(--white)}
.svc .ph{height:186px}
.svc h3{font-size:18px;color:var(--ink);text-align:center;margin-top:14px}
.svc .btn{position:absolute;left:101px;top:258px;width:100px;height:22px;border-radius:0;font-size:10px}
.nav-circle{position:absolute;width:30px;height:30px;border-radius:50%;background:var(--white);display:flex;align-items:center;justify-content:center}

/* testimonial */
.card-back{position:absolute;border-radius:8px}
.quote{left:618px;top:2012px;width:470px;font-size:14.5px;line-height:26px}

/* blog */
.post{position:absolute;background:var(--white);box-shadow:0 3px 14px rgba(0,0,0,.12)}
.post h4{position:absolute;font-size:19px;line-height:27px;color:var(--ink)}
.post .date{position:absolute;font-size:14px;color:var(--muted);display:flex;gap:8px;align-items:center}
.post .more{position:absolute;font-size:13px;font-weight:700;color:var(--blue);text-transform:uppercase}

/* contact */
.field{position:absolute;height:54px;background:var(--field);border-radius:27px;box-shadow:0 2px 10px rgba(0,0,0,.12);font-size:13px;color:#666;padding:20px 28px}

/* footer */
.footer{position:absolute;left:0;top:4766px;width:1200px;height:389px;background:var(--footer);color:var(--white)}
.footer h5{position:absolute;font-family:"Michroma",sans-serif;font-size:15px;letter-spacing:1.5px;font-weight:400}
.footer ul{position:absolute;list-style:none;font-size:14px;line-height:26px}
.footer .line{position:absolute;display:flex;gap:12px;font-size:14px;line-height:24px}
.soc{position:absolute;width:40px;height:40px;border-radius:50%}
</style>
</head>
<body>

<!-- Header -->
<header class="header">
  <div class="menu"><i></i><i></i><i></i></div>
  <div class="ring" style="left:746px;top:38px;width:40px;height:40px"></div>
  <div class="ring" style="left:796px;top:38px;width:40px;height:40px"></div>
  <div class="ring" style="left:846px;top:38px;width:40px;height:40px"></div>
  <div class="ring" style="left:896px;top:38px;width:40px;height:40px"></div>
  <div class="btn" style="left:960px;top:38px;width:128px;height:42px">Contact</div>
</header>
<div class="brand"><span>TRI-BAY<br>GROUP</span></div>

<!-- Hero -->
<section class="hero" role="img" aria-label="Contractor reviewing plans with yellow hard hat on the table"></section>
<h1 class="display hero-title">WE OFFER RELIABLE<br><span class="hl">“WORD-OF-MOUTH”</span><br>EVIDENCE OF QUALITY<br>WORKMANSHIP</h1>
<div class="btn" style="left:110px;top:500px;width:190px;height:38px">Download Resources</div>
<div class="dots" style="left:572px;top:612px"><i></i><i class="on"></i><i></i></div>

<!-- About -->
<div class="photo about-img" role="img" aria-label="Modern gabled house with glass facade"></div>
<h2 class="display abs" style="left:598px;top:774px;font-size:28px">ABOUT <span class="hl">TRI-BAY GROUP</span></h2>
<p class="abs about-text">Lorem ipsum dolor sit amet, consectetur adipiscing elit, sed do eiusmod tempor incididunt ut labore et dolore magna aliqua. Ut enim ad minim veniam, quis nostrud exercitation ullamco laboris nisi ut aliquip ex ea commodo consequat. Duis aute irure dolor in reprehenderit in voluptate velit esse cillum dolore eu fugiat nulla pariatur. Excepteur sint occaecat cupidatat non proident, sunt in culpa qui officia deserunt mollit anim id est laborum.</p>
<div class="btn" style="left:598px;top:1056px;width:138px;height:40px">Learn More</div>

<!-- Services -->
<section class="band" style="top:1202px;height:558px;background:linear-gradient(180deg,var(--blue),#1677dd)"></section>
<h2 class="display abs" style="left:0;width:1200px;text-align:center;top:1284px;font-size:28px;color:var(--white)">OUR SERVICES</h2>
<div class="svc" style="left:110px"><div class="ph" role="img" aria-label="Handshake over plans with hard hat" style="background:linear-gradient(135deg,#e8e4dc,#9c968c)"></div><h3 class="cond">General Contractors</h3><div class="btn">Read More</div></div>
<div class="svc" style="left:448px"><div class="ph" role="img" aria-label="Bathroom under renovation" style="background:linear-gradient(135deg,#f2f2f0,#b9bcbf)"></div><h3 class="cond">Home Renovations</h3><div class="btn">Read More</div></div>
<div class="svc" style="left:786px"><div class="ph" role="img" aria-label="Workers on commercial building site" style="background:linear-gradient(135deg,#a7b3bb,#6e6c66)"></div><h3 class="cond">Commercial Construction</h3><div class="btn">Read More</div></div>
<div class="nav-circle" style="left:56px;top:1502px"><svg width="14" height="14" viewBox="0 0 14 14"><path d="M9 2 4 7l5 5" stroke="#1a7fe6" stroke-width="2.5" fill="none"/></svg></div>
<div class="nav-circle" style="left:1114px;top:1502px"><svg width="14" height="14" viewBox="0 0 14 14"><path d="m5 2 5 5-5 5" stroke="#1a7fe6" stroke-width="2.5" fill="none"/></svg></div>

<!-- Testimonials -->
<div class="card-back" style="left:114px;top:1874px;width:380px;height:370px;background:#dfe5ee"></div>
<div class="card-back" style="left:128px;top:1858px;width:380px;height:370px;background:#eceff3"></div>
<div class="card-back" style="left:146px;top:1842px;width:374px;height:372px;background:var(--white);box-shadow:0 4px 14px rgba(0,0,0,.15);overflow:hidden">
  <div role="img" aria-label="Portrait of smiling client with crossed arms" style="height:284px;background:linear-gradient(160deg,#d9d9d9,#a9a9a9)"></div>
  <p class="display" style="text-align:center;margin-top:22px;font-size:16px;color:#777">DANIEL REYES</p>
  <p style="text-align:center;color:#f5b800;font-size:15px;letter-spacing:2px">★★★★★</p>
</div>
<h2 class="display abs" style="left:618px;top:1882px;font-size:28px;line-height:44px">WHAT PEOPLE<br><span class="hl">ARE SAY</span></h2>
<div class="abs" style="left:618px;top:1984px;width:470px;height:2px;background:#9ec6f2"></div>
<p class="abs quote">“Lorem ipsum dolor sit amet, consectetur adipiscing elit, sed do eiusmod tempor incididunt ut labore et dolore magna aliqua. Ut enim ad minim veniam, quis nostrud exercitation ullamco laboris nisi ut aliquip ex ea commodo consequat.”</p>
<div class="dots" style="left:618px;top:2170px;gap:6px"><i style="background:#cfe2f6"></i><i class="on"></i><i style="background:#cfe2f6"></i><i style="background:#cfe2f6"></i><i style="background:#cfe2f6"></i><i style="background:#cfe2f6"></i></div>

<!-- Portfolio -->
<section class="band" style="top:2330px;height:670px"></section>
<h2 class="display abs" style="left:110px;top:2416px;font-size:28px;color:var(--white)">OUR PORTFOLIO</h2>
<div class="abs" style="left:952px;top:2414px;width:64px;height:38px;background:var(--white);border-radius:3px;display:flex;align-items:center;justify-content:center"><svg width="24" height="16" viewBox="0 0 24 16"><path d="M23 8H2M8 2 2 8l6 6" stroke="#1a7fe6" stroke-width="2.5" fill="none"/></svg></div>
<svg class="abs" style="left:1042px;top:2425px" width="24" height="16" viewBox="0 0 24 16"><path d="M1 8h21M16 2l6 6-6 6" stroke="#fff" stroke-width="2.5" fill="none"/></svg>
<div class="photo" style="left:0;top:2498px;width:382px;height:412px;background:linear-gradient(180deg,#3f82d6,#9dbfe4)" role="img" aria-label="Crane lifting a unit onto a rooftop"></div>
<div class="photo" style="left:408px;top:2498px;width:382px;height:412px;background:linear-gradient(180deg,#e6e6e4,#a5a29c)" role="img" aria-label="Worker inspecting a gutted interior"></div>
<div class="photo" style="left:818px;top:2498px;width:382px;height:412px;background:linear-gradient(180deg,#c9d3dd,#7d766b)" role="img" aria-label="Workers in safety vests at a steel frame site"></div>

<!-- Blog -->
<h2 class="display abs" style="left:0;width:1200px;text-align:center;top:3078px;font-size:28px">LATEST <span class="hl">BLOG</span></h2>
<article class="post" style="left:110px;top:3152px;width:490px;height:500px">
  <div class="photo" style="left:14px;top:14px;width:464px;height:318px;background:linear-gradient(160deg,#f0ede8,#b9aa94)" role="img" aria-label="Framed room with vanity and bathtub"></div>
  <h4 class="cond" style="left:14px;top:354px">Sed ut perspiciatis unde omnis iste natus error</h4>
  <div class="date" style="left:14px;top:396px"><svg width="13" height="13" viewBox="0 0 13 13"><rect x="1" y="2" width="11" height="10" fill="#aaa"/></svg>April 27,2023</div>
  <div class="more" style="left:14px;top:454px">Read More →</div>
</article>
<article class="post" style="left:634px;top:3152px;width:454px;height:240px">
  <div class="photo" style="left:10px;top:10px;width:192px;height:220px;background:linear-gradient(160deg,#b8c3cc,#5b5850)" role="img" aria-label="Workers in hard hats at a city site"></div>
  <h4 class="cond" style="left:230px;top:38px;color:var(--blue)">Sed ut perspiciatis<br>unde omnis iste</h4>
  <div class="date" style="left:230px;top:112px"><svg width="13" height="13" viewBox="0 0 13 13"><rect x="1" y="2" width="11" height="10" fill="#aaa"/></svg>April 27,2023</div>
  <div class="more" style="left:230px;top:184px">Read More →</div>
</article>
<article class="post" style="left:634px;top:3412px;width:454px;height:240px">
  <div class="photo" style="left:10px;top:10px;width:192px;height:220px;background:linear-gradient(160deg,#8a7a66,#d4d2ce)" role="img" aria-label="Woman reviewing plans on a wall"></div>
  <h4 class="cond" style="left:230px;top:38px">Sed ut perspiciatis<br>unde omnis iste</h4>
  <div class="date" style="left:230px;top:112px"><svg width="13" height="13" viewBox="0 0 13 13"><rect x="1" y="2" width="11" height="10" fill="#aaa"/></svg>April 27,2023</div>
  <div class="more" style="left:230px;top:184px">Read More →</div>
</article>

<!-- Media gallery -->
<section class="band" style="top:3736px;height:468px"></section>
<h2 class="display abs" style="left:0;width:1200px;text-align:center;top:3812px;font-size:28px;color:var(--white)">MEDIA GALLERY</h2>
<div class="photo" style="left:112px;top:3904px;width:228px;height:216px;background:linear-gradient(160deg,#4c4a3a,#d7c83a)" role="img" aria-label="Engineer in hard hat and hi-vis vest"></div>
<div class="photo" style="left:362px;top:3904px;width:228px;height:216px;background:linear-gradient(160deg,#6f6e6b,#3f3e3b)" role="img" aria-label="Hard hat and plans on a desk"></div>
<div class="photo" style="left:610px;top:3904px;width:228px;height:216px;background:linear-gradient(160deg,#b9c7cc,#7a6c5e)" role="img" aria-label="Worker on ladder in interior renovation"></div>
<div class="photo" style="left:860px;top:3904px;width:228px;height:216px;background:linear-gradient(160deg,#f1efea,#c3bcb0)" role="img" aria-label="Woman applying wallpaper"></div>

<!-- Contact -->
<h2 class="display abs" style="left:0;width:1200px;text-align:center;top:4282px;font-size:28px">CONTACT <span class="hl">US</span></h2>
<div class="field" style="left:168px;top:4376px;width:424px">First Name :</div>
<div class="field" style="left:606px;top:4376px;width:424px">Last Name :</div>
<div class="field" style="left:168px;top:4456px;width:424px">Email :</div>
<div class="field" style="left:606px;top:4456px;width:424px">Phone :</div>
<div class="field" style="left:168px;top:4540px;width:862px">Message :</div>
<div class="btn" style="left:516px;top:4628px;width:168px;height:56px;border-radius:28px;font-size:16px">Submit</div>

<!-- Footer -->
<footer class="footer">
  <div class="abs" style="left:122px;top:92px;width:200px;height:200px;border-radius:50%;border:6px solid #fff;display:flex;align-items:center;justify-content:center"><span style="font-family:'Michroma',sans-serif;font-size:20px;text-align:center;line-height:30px">TRI-BAY<br>GROUP</span></div>
  <h5 style="left:390px;top:88px">QUICK LINKS</h5>
  <ul style="left:390px;top:126px"><li>Home</li><li>About Us</li><li>Services</li><li>Testimonials</li><li>Gallery</li><li>Contact Us</li></ul>
  <h5 style="left:586px;top:88px">CONTACT US</h5>
  <div class="line" style="left:586px;top:128px"><svg width="14" height="18" viewBox="0 0 14 18"><path d="M7 0a7 7 0 0 0-7 7c0 5 7 11 7 11s7-6 7-11a7 7 0 0 0-7-7z" fill="#fff"/><circle cx="7" cy="7" r="2.5" fill="#262626"/></svg><span>Lorem ipsum dolor<br>sit amet</span></div>
  <div class="line" style="left:586px;top:196px"><svg width="16" height="16" viewBox="0 0 16 16"><path d="M3 1l3 3-2 2c1 2 3 4 5 5l2-2 3 3-2 3C6 15 1 10 1 3z" fill="#fff"/></svg><span>+1 (555) 014 2290</span></div>
  <div class="line" style="left:586px;top:230px"><svg width="16" height="16" viewBox="0 0 16 16"><rect x="1" y="3" width="14" height="10" fill="#fff"/><path d="M1 3l7 6 7-6" stroke="#262626" fill="none"/></svg><span>info@tribaygroup.com</span></div>
  <h5 style="left:854px;top:88px">NEWSLETTER</h5>
  <div class="abs" style="left:854px;top:136px;width:172px;height:36px;background:#fff;color:#888;font-size:13px;padding:9px 14px">Enter email</div>
  <div class="abs" style="left:1026px;top:136px;width:54px;height:36px;background:var(--blue);display:flex;align-items:center;justify-content:center"><svg width="16" height="12" viewBox="0 0 16 12"><rect width="16" height="12" fill="#fff"/><path d="M0 0l8 6 8-6" stroke="#1a7fe6" fill="none"/></svg></div>
  <div class="soc" style="left:874px;top:220px;background:var(--blue)"></div>
  <div class="soc" style="left:928px;top:220px;background:var(--blue)"></div>
  <div class="soc" style="left:982px;top:220px;background:var(--blue)"></div>
  <div class="soc" style="left:1038px;top:220px;background:var(--blue)"></div>
  <p class="abs" style="left:0;width:1200px;text-align:center;top:332px;font-size:14px">©Copyrights 2023 Tri-Bay Group &nbsp;| &nbsp; All Rights Reserved</p>
</footer>

</body>
</html>
```